New Business Cards for Tormin Group

We need a new Business Card to compliment our new logo. We are a vibrant design, manufacture and install business providing recreation areas, public parks and Municipal spaces. We want business cards that are classy, modern and clean.

We have recently changed our logo, and are celebrating our 40th anniversary. We want business cards with a new modern design to reflect our status.

Target Market(s)

Customers

Contact Information for Business Card

We need all the details of our 3 offices as per the business card attached. Please disregard the old logo on the business card, the other three files show our new logo.

Requirements
Must have
• All info as per attached business card but with new logo.
Nice to have

```html
<!DOCTYPE html>
<html lang="en">
<head>
<meta charset="utf-8">
<title>Tormin Group – Business Card</title>
<link rel="stylesheet" href="https://fonts.googleapis.com/css2?family=Lato:wght@400;700;900&display=swap">
<style>
  :root {
    --bg: #5e5e5e;
    --card: #ffffff;
    --red: #e8303a;
    --red-dark: #b3222a;
    --ink: #3d3d3d;
    --muted: #555555;
    --rule: #8a8a8a;
    --base: #3a3a3a;
    --faint: #f0f0f0;
  }
  * { margin: 0; padding: 0; box-sizing: border-box; }
  html, body { width: 1200px; height: 1200px; overflow: hidden; }
  body {
    background: var(--bg);
    font-family: "Lato", Arial, sans-serif;
    position: relative;
  }
  .card {
    position: absolute;
    left: 100px; top: 309px;
    width: 1000px; height: 582px;
    background: var(--card);
    border-radius: 30px;
    overflow: hidden;
  }
  .card-base {
    position: absolute; left: 0; right: 0; bottom: 0; height: 29px;
    background: var(--base);
  }
  .globe-decor {
    position: absolute;
    left: 581px; top: -39px;
    width: 384px; height: 384px;
    border-radius: 50%;
    background: radial-gradient(circle, #f4f4f4 0%, var(--faint) 70%, #ececec 100%);
  }
  .name-tab {
    position: absolute; left: 0; top: 101px;
    width: 14px; height: 77px;
    background: var(--red);
    border-radius: 0 5px 5px 0;
  }
  .brand {
    position: absolute; left: 690px; top: 96px;
    display: flex; align-items: center; gap: 14px;
  }
  .brand-dot { width: 58px; height: 58px; border-radius: 50%; background: var(--red); }
  .brand-name {
    font-weight: 900; font-size: 36px; color: var(--ink);
    letter-spacing: 0.5px;
  }
  .holder { position: absolute; left: 37px; top: 104px; }
  .holder-name { font-size: 37px; font-weight: 700; color: var(--red); line-height: 1.1; }
  .holder-title { font-size: 25px; color: var(--ink); margin-top: 8px; }
  .contact { position: absolute; left: 37px; top: 224px; font-size: 23px; color: var(--ink); line-height: 38px; }
  .contact .label { color: var(--red); }
  .divider {
    position: absolute; left: 37px; top: 317px;
    width: 914px; height: 2px; background: var(--rule);
  }
  .office { position: absolute; top: 342px; }
  .office-title { font-size: 23px; color: var(--red); margin-bottom: 10px; }
  .office-lines { font-size: 17px; color: var(--muted); line-height: 24px; }
  .office-lines .gap { margin-top: 4px; display: block; }
  .office.head { left: 37px; }
  .office.dubai { left: 382px; }
  .office.qatar { left: 700px; top: 346px; }
  .ribbon { position: absolute; left: 0; top: 0; width: 1000px; height: 582px; }
  .web {
    position: absolute; left: 273px; width: 452px; top: 525px;
    text-align: center; color: #fff; font-size: 23px;
  }
</style>
</head>
<body>
  <main class="card">
    <div class="globe-decor" role="img" aria-label="Faint world globe decoration"></div>
    <div class="card-base"></div>

    <div class="name-tab"></div>
    <div class="holder">
      <h1 class="holder-name">Samir Haddad</h1>
      <p class="holder-title">Managing Partner</p>
    </div>

    <div class="brand">
      <div class="brand-dot"></div>
      <span class="brand-name">TORMIN GROUP</span>
    </div>

    <div class="contact">
      <p><span class="label">Phone</span>: +971 (0)50 318 4720</p>
      <p><span class="label">Email</span>: samir@tormingroup.com</p>
    </div>

    <div class="divider"></div>

    <section class="office head">
      <h2 class="office-title">Head Office</h2>
      <p class="office-lines">P.O. Box: 41820<br>Abu Dhabi. U.A.E<br>Tel No: +971 (0)2 5538102<span class="gap">Fax No: +971(0)2 5538103</span></p>
    </section>
    <section class="office dubai">
      <h2 class="office-title">Dubai Office</h2>
      <p class="office-lines">P.O. Box: 207416<br>Dubai, U.A.E<br>Tel No: +971 (0)4 382157<span class="gap">Fax No: +971(0)4 382164</span></p>
    </section>
    <section class="office qatar">
      <h2 class="office-title">Qater Office</h2>
      <p class="office-lines">P.O. Box: 30972<br>Doha, Qatter<br>Tel No: +974 44718306<span class="gap">Fax No: +971 44720514</span></p>
    </section>

    <svg class="ribbon" viewBox="0 0 1000 582" aria-hidden="true">
      <polygon points="249,545 273,521 273,545" fill="var(--red-dark)"/>
      <polygon points="751,545 725,521 725,545" fill="var(--red-dark)"/>
      <polygon points="273,521 725,521 710,582 288,582" fill="var(--red)"/>
    </svg>
    <p class="web">www.tormingroup.com</p>
  </main>
</body>
</html>
```